Banner to be displayed at local Farmers Market Booth.

Graphic Design Brief: Farmers Market Banner Contest

Project Overview:We are seeking talented graphic designers to create a visually appealing banner for our booth at the local farmers market. Our company specializes in healthy, all-natural dog and cat treats, and we want a banner that captures our brand identity while drawing in pet owners who value quality and nutrition for their furry friends.

Banner Specifications:

Size: 24 inches x 60 inches (Horizontal orientation) 24" High X 60 wide

Theme: Vintage/Retro

Style: Warm, inviting, nostalgic with a touch of rustic charm

Colors: Earthy, muted tones such as warm browns, soft greens, and creamy yellows. Pops of red or blue may be used sparingly for accents. OR Black and White with gray scales. Would like to see both

Typography: Retro-style fonts that are readable and align with the vintage aesthetic.

Key Elements to Include: website (www.moltbyfarms.com)

Company Name: Moltby Farms

Tagline: " Simply Honest Bites "
Imagery: Illustrations or stylized graphics of happy dogs and cats, possibly interacting with treats.

Emphasis on Natural Ingredients: Icons or design elements that subtly suggest freshness and quality (e.g., leaves, wheat, bones, or paw prints).

Farmers Market Appeal: A design that blends well with the artisanal, handmade, and farm-fresh atmosphere of the market.

Design Considerations:

The banner should be easily readable from a distance.

A balanced composition that doesn't feel overcrowded.

Should evoke trust and warmth while maintaining a professional look.

Avoid overly modern or sleek elements that don’t align with the vintage aesthetic.

Submission Requirements:

High-resolution digital file in PDF or AI format.

CMYK color mode for printing purposes.

Must include a mockup or preview of how it would look in a real farmers market setting.

We look forward to seeing your creative interpretations of our brand! If you have any questions, feel free to reach out.

Font styles to use
Other font styles liked:
• See attachement

Requirements
Nice to have
• Retro/Vintage,playful BUT NOT whimsical

```html
<!DOCTYPE html>
<html lang="en">
<head>
<meta charset="utf-8">
<title>Moltby Farms – Market Banner</title>
<link rel="stylesheet" href="https://fonts.googleapis.com/css2?family=Montserrat:wght@700;800&display=swap">
<style>
  :root {
    --page-bg: #e8ebee;
    --banner-white: #ffffff;
    --tan: #b89e74;
    --ink: #1d1d1b;
    --sketch-light: #f4f1ec;
    --sketch-mid: #e2dbcf;
  }
  html, body {
    margin: 0;
    width: 1200px;
    height: 900px;
    overflow: hidden;
    background: var(--page-bg);
  }
  .banner {
    position: absolute;
    left: 50px;
    top: 230px;
    width: 1100px;
    height: 440px;
    background: var(--banner-white);
    overflow: hidden;
    box-shadow: 0 6px 24px rgba(0,0,0,0.12);
  }
  .banner__shapes {
    position: absolute;
    inset: 0;
  }
  .tagline,
  .brand-name,
  .website {
    position: absolute;
    left: 340px;
    width: 540px;
    margin: 0;
    text-align: center;
    color: var(--ink);
    font-family: "Montserrat", sans-serif;
    font-weight: 800;
    white-space: nowrap;
    line-height: 1.1;
  }
  .tagline {
    top: 38px;
    font-size: 46px;
    letter-spacing: 0.5px;
  }
  .brand-name {
    top: 180px;
    font-size: 60px;
  }
  .website {
    top: 352px;
    font-size: 36px;
    font-weight: 700;
    letter-spacing: 0.5px;
  }
</style>
</head>
<body>
  <section class="banner" aria-label="Moltby Farms market banner">
    <svg class="banner__shapes" width="1100" height="440" viewBox="0 0 1100 440">
      <defs>
        <linearGradient id="sketch-tone" x1="0" y1="0" x2="0" y2="1">
          <stop offset="0" stop-color="var(--sketch-light)"/>
          <stop offset="1" stop-color="var(--sketch-mid)"/>
        </linearGradient>
      </defs>
      <path class="blob blob--left" fill="var(--tan)"
            d="M0 0 H165 C140 60 200 110 280 140 C360 170 330 250 318 300 C305 355 345 390 300 440 H0 Z"/>
      <path class="blob blob--right" fill="var(--tan)"
            d="M900 150 C950 125 1020 130 1060 145 L1100 145 V395 C1040 390 1005 365 1000 325 C995 285 1010 260 985 232 C955 200 890 190 900 150 Z"/>
      <rect class="illustration illustration--dog" role="img"
            aria-label="Ink sketch of a standing beagle looking up toward the tagline"
            x="75" y="80" width="200" height="320" rx="10" fill="url(#sketch-tone)" opacity="0.85"/>
      <rect class="illustration illustration--cat" role="img"
            aria-label="Ink sketch of a smiling striped kitten sitting"
            x="920" y="160" width="100" height="165" rx="10" fill="url(#sketch-tone)" opacity="0.85"/>
    </svg>

    <h2 class="tagline">Simply Honest Bites</h2>
    <h1 class="brand-name">Moltby Farms</h1>
    <p class="website">www.moltbyfarms.com</p>
  </section>
</body>
</html>
```